Corvane Business Cards

Front of business card will have logo, name, address, & telephone number. Back of card will have a list of services provided - Roads, Substation Pads, Temporary Pads, Site Pads, Land Leveling, Powerline Row Cleaning, Land Clearing, Gates, Fencing, Construction Entrances, Excavation, Trenching, Underground Utilities, Directional Boring, Pile Driving. We are a construction company that uses heavy equipment like bulldozers, motor graders/blades, dump trucks, backhoes, hydro axes, & skid loaders. We build roads, pads, & install electric utility lines & waterlines underground. This logo is new. The word "Construction" can be smaller as uploaded 2 example edited logos. We will be using this card design for many employees.
Target Market(s)
Industrial Electric Powerline, Wind Turbine, Solar Panel, & Water Utility companies.
Contact Information for Business Card
Name/Position - Dwayne Halster - Owner
Address: 4875 FM 309
Ridgeway, NM 88041
Phone number - (555) 482-5096

```html
<!DOCTYPE html>
<html lang="en">
<head>
<meta charset="utf-8">
<title>Corvane Construction – Business Card</title>
<link href="https://fonts.googleapis.com/css2?family=Cinzel:wght@600;700&family=Roboto:wght@400;500&display=swap" rel="stylesheet">
<style>
  :root{
    --maroon:#3b1119;
    --maroon-deep:#2c0c12;
    --ink:#2a0b11;
    --paper:#ffffff;
    --stage:#e6eaea;
    --on-dark:#ffffff;
  }
  *{box-sizing:border-box;margin:0;padding:0}
  html,body{width:1200px;height:900px;overflow:hidden;background:var(--stage)}
  .stage{width:1200px;height:900px;display:flex;align-items:center;justify-content:center;gap:40px}
  .card{width:540px;height:309px;position:relative;overflow:hidden;box-shadow:0 6px 18px rgba(0,0,0,.12)}

  .card-front{background:var(--paper);color:var(--ink)}
  .card-front .base-band{position:absolute;left:0;right:0;bottom:0;height:14px;background:var(--maroon)}

  .company{font-family:'Cinzel',serif;font-weight:700;line-height:1.05;letter-spacing:.5px}
  .company .line-1{display:block;font-size:30px}
  .company .line-2{display:block;font-size:21px}
  .card-front .company{position:absolute;left:34px;top:32px;color:var(--ink)}

  .person{position:absolute;left:34px;top:140px;padding-left:12px;border-left:3px solid var(--ink)}
  .person .name{font-family:'Cinzel',serif;font-weight:700;font-size:20px;letter-spacing:.5px;line-height:1.1}
  .person .role{font-family:'Roboto',sans-serif;font-weight:400;font-size:12px;letter-spacing:.6px}

  .contact{position:absolute;display:flex;align-items:center;gap:9px;font-family:'Roboto',sans-serif;font-weight:400;font-size:15px;letter-spacing:.6px;color:var(--ink);white-space:nowrap}
  .contact svg{width:18px;height:18px;flex:none}
  .contact-phone{left:34px;bottom:44px}
  .contact-address{right:30px;bottom:80px}

  .card-back{background:linear-gradient(135deg,var(--maroon) 0%,var(--maroon-deep) 100%);color:var(--on-dark)}
  .card-back .company{position:absolute;right:30px;top:38px;text-align:right;color:var(--on-dark)}

  .services{position:absolute;left:30px;bottom:26px;list-style:none;font-family:'Roboto',sans-serif;font-weight:400;font-size:12.5px;line-height:17.2px;letter-spacing:.4px}
  .services li{display:flex;align-items:center;gap:8px}
  .services li::before{content:"";width:6px;height:6px;border-radius:50%;background:var(--on-dark)}
</style>
</head>
<body>
<main class="stage">
  <section class="card card-front" aria-label="Card front">
    <div class="company"><span class="line-1">CORVANE</span><span class="line-2">CONSTRUCTION</span></div>
    <div class="person">
      <div class="name">DWAYNE HALSTER</div>
      <div class="role">Owner</div>
    </div>
    <div class="contact contact-address">
      <svg viewBox="0 0 20 20" aria-hidden="true"><circle cx="10" cy="10" r="10" fill="var(--ink)"/><path d="M10 4.5a3.6 3.6 0 0 0-3.6 3.6c0 2.7 3.6 6.9 3.6 6.9s3.6-4.2 3.6-6.9A3.6 3.6 0 0 0 10 4.5z" fill="#fff"/><circle cx="10" cy="8.1" r="1.4" fill="var(--ink)"/></svg>
      <span>4875 FM 309, Ridgeway, NM 88041</span>
    </div>
    <div class="contact contact-phone">
      <svg viewBox="0 0 20 20" aria-hidden="true"><circle cx="10" cy="10" r="10" fill="var(--ink)"/><path d="M7.2 5.2l1.5 2.2-1 1a6 6 0 0 0 3.9 3.9l1-1 2.2 1.5-.9 1.6c-3.9.2-8-3.9-7.8-7.8z" fill="#fff"/></svg>
      <span>(555) 482-5096</span>
    </div>
    <div class="base-band"></div>
  </section>

  <section class="card card-back" aria-label="Card back">
    <ul class="services">
      <li>Roads</li>
      <li>Substation Pads</li>
      <li>Temporary Pads</li>
      <li>Site Pads</li>
      <li>Land Leveling</li>
      <li>Powerline Row Cleaning</li>
      <li>Land Clearing</li>
      <li>Gates</li>
      <li>Fencing</li>
      <li>Construction Entrances</li>
      <li>Excavation</li>
      <li>Trenching</li>
      <li>Underground Utilities</li>
      <li>Directional Boring</li>
      <li>Pile Driving</li>
    </ul>
    <div class="company"><span class="line-1">CORVANE</span><span class="line-2">CONSTRUCTION</span></div>
  </section>
</main>
</body>
</html>
```